Design 4 pages for an event discovery website

This is a contest for the design of 4 pages for an events discovery website. The feature is part of the new sign-up process.

Please see the attached document for a full scope, mockups and the parent category icons.

Target Market(s)

18-35 Australian event goers

Industry/Entity Type

Events

Number of Pages Required

4 page

```html
<!DOCTYPE html>
<html lang="en">
<head>
<meta charset="utf-8">
<title>Gigwave – Sign Up</title>
<link href="https://fonts.googleapis.com/css2?family=Maven+Pro:wght@400;500&family=Yanone+Kaffeesatz:wght@300;400;600&family=Open+Sans:wght@400&display=swap" rel="stylesheet">
<style>
:root{
  --brand-blue:#5a72b8;
  --brand-dark:#3a3f4a;
  --panel-blue:rgba(92,110,176,.9);
  --connect-blue:#5068b0;
  --signup-cyan:#1ba9dc;
  --login-amber:#f0b02e;
  --tick-green:#6fae2c;
  --footer-bg:#141414;
  --footer-text:#d6d6d6;
  --text-dark:#4a4f58;
}
*{margin:0;padding:0;box-sizing:border-box}
html,body{width:1200px;height:831px;overflow:hidden}
body{position:relative;font-family:"Maven Pro",sans-serif;background:#dfe6ea}
.hero-photo{position:absolute;left:0;top:0;width:1200px;height:705px;
  background:linear-gradient(160deg,#d8e0e6 0%,#b9cfd9 35%,#9fc3d0 55%,#d9cdb8 80%,#c9b59c 100%)}
.hero-photo::after{content:"";position:absolute;inset:0;background:rgba(255,255,255,.35)}
.site-header{position:absolute;left:0;top:0;width:1200px;height:118px;background:rgba(255,255,255,.86);border-bottom:1px solid #dde2e6}
.brand{position:absolute;left:99px;top:38px;font-family:"Maven Pro",sans-serif;font-weight:500;font-size:40px;letter-spacing:1px;color:var(--brand-dark)}
.main-nav{position:absolute;left:492px;top:48px;display:flex}
.main-nav a{font-size:18px;color:#444;text-decoration:none;padding:0 23px;border-right:1px solid #e3e3e3;line-height:26px}
.search-box{position:absolute;left:698px;top:41px;width:190px;height:36px;background:#fff;border:1px solid #e0e0e0;border-radius:2px;padding-left:13px;font-size:15px;color:#888;line-height:34px}
.btn{position:absolute;top:42px;width:92px;height:34px;border-radius:2px;color:#fff;font-size:13px;font-weight:500;text-align:center;line-height:34px}
.btn-signup{left:907px;background:var(--signup-cyan)}
.btn-login{left:1010px;background:var(--login-amber)}
.signup-card{position:absolute;left:99px;top:222px;width:402px;height:354px;background:rgba(255,255,255,.78);border:1px solid #e3e6e8}
.signup-title{position:absolute;left:25px;top:35px;font-family:"Yanone Kaffeesatz",sans-serif;font-weight:600;font-size:62px;color:var(--brand-blue);line-height:1}
.connect-btn{position:absolute;left:25px;top:124px;width:352px;height:143px;background:linear-gradient(180deg,#5a76c2,#4a62a8);border-radius:3px;color:#fff;overflow:hidden}
.connect-icon{position:absolute;left:0;top:0;width:97px;height:143px;border-right:1px solid rgba(0,0,0,.15)}
.connect-icon span{position:absolute;left:30px;top:53px;width:36px;height:36px;background:#fff;border-radius:2px}
.connect-label{position:absolute;left:120px;top:24px;width:226px;font-size:26px;line-height:48px;white-space:nowrap}
.benefits{position:absolute;left:528px;top:222px;width:573px;height:357px;background:var(--panel-blue);color:#fff}
.benefits h2{position:absolute;left:32px;top:22px;font-family:"Yanone Kaffeesatz",sans-serif;font-weight:600;font-size:64px;line-height:1}
.benefits ul{position:absolute;left:32px;top:116px;list-style:none;font-family:"Yanone Kaffeesatz",sans-serif;font-weight:300;font-size:20px}
.benefits li{height:34.3px;display:flex;align-items:center;white-space:nowrap}
.benefits li svg{margin-right:20px;flex:none}
.no-social{position:absolute;left:99px;top:627px;display:flex;align-items:center;font-size:20px;color:var(--text-dark)}
.no-social svg{margin-right:12px}
.site-footer{position:absolute;left:0;top:705px;width:1200px;height:126px;background:var(--footer-bg);font-family:"Open Sans",sans-serif;color:var(--footer-text);text-align:center}
.footer-links{margin-top:18px;font-size:13px}
.footer-links span{margin:0 7px}
.copyright{margin-top:12px;font-size:13px}
.social-row{display:flex;justify-content:center;gap:5px;margin-top:9px}
.social-row i{width:29px;height:29px;border:1.5px solid #ddd;border-radius:50%}
</style>
</head>
<body>
<div class="hero-photo" role="img" aria-label="Soft-focus photo of a smiling man in sunglasses working on a laptop at the beach"></div>

<header class="site-header">
  <div class="brand">GIGWAVE</div>
  <nav class="main-nav"><a>Find</a><a>Events</a></nav>
  <div class="search-box">Search</div>
  <div class="btn btn-signup">SIGN UP</div>
  <div class="btn btn-login">LOGIN</div>
</header>

<section class="signup-card">
  <h1 class="signup-title">Sign Up</h1>
  <div class="connect-btn">
    <div class="connect-icon"><span></span></div>
    <div class="connect-label">Connect<br>With Circlebook</div>
  </div>
</section>

<section class="benefits">
  <h2>Benefits</h2>
  <ul>
    <li><svg width="13" height="13"><circle cx="6.5" cy="6.5" r="5.3" fill="none" stroke="#fff" stroke-width="2"/><circle cx="6.5" cy="6.5" r="2.2" fill="#fff"/></svg>Get personalised event recommendations</li>
    <li><svg width="13" height="13"><circle cx="6.5" cy="6.5" r="5.3" fill="none" stroke="#fff" stroke-width="2"/><circle cx="6.5" cy="6.5" r="2.2" fill="#fff"/></svg>Get notified about your favourite events - never miss out again</li>
    <li><svg width="13" height="13"><circle cx="6.5" cy="6.5" r="5.3" fill="none" stroke="#fff" stroke-width="2"/><circle cx="6.5" cy="6.5" r="2.2" fill="#fff"/></svg>Follow all your favourite artists, musicians, teams and players in one place</li>
    <li><svg width="13" height="13"><circle cx="6.5" cy="6.5" r="5.3" fill="none" stroke="#fff" stroke-width="2"/><circle cx="6.5" cy="6.5" r="2.2" fill="#fff"/></svg>Follow your favourite local venues to know everything happening there</li>
    <li><svg width="13" height="13"><circle cx="6.5" cy="6.5" r="5.3" fill="none" stroke="#fff" stroke-width="2"/><circle cx="6.5" cy="6.5" r="2.2" fill="#fff"/></svg>Get curated news and feature content on your favourite artists (coming soon)</li>
    <li><svg width="13" height="13"><circle cx="6.5" cy="6.5" r="5.3" fill="none" stroke="#fff" stroke-width="2"/><circle cx="6.5" cy="6.5" r="2.2" fill="#fff"/></svg>Invite your mates to events via Circlebook (CB sign-up only)</li>
  </ul>
</section>

<div class="no-social">
  <svg width="20" height="20"><rect width="20" height="20" rx="3" fill="var(--tick-green)"/><path d="M5 10.5l3.5 3.5L15 7" fill="none" stroke="#fff" stroke-width="2.6"/></svg>
  Click Here to sign up without Circlebook
</div>

<footer class="site-footer">
  <div class="footer-links">Find<span>/</span>Events<span>/</span>About Us<span>/</span>Search<span>/</span>Register<span>/</span>Contact Us</div>
  <div class="copyright">©2013 - 2014 &nbsp;gigwave.com, All Rights Reserved.</div>
  <div class="social-row"><i></i><i></i><i></i><i></i><i></i></div>
</footer>
</body>
</html>
```